Podiatry clinic requires a modern revamp and editing of existing website.

I would like a fresh new look and updated information for my current business website. An easy to navigate site with prominent address and phone number for call to action. We are a podiatry clinic that focuses on general and sports podiatry.
I would like 4 pages; including Home page, About Us, Services & Contact.
www.brambleridgepodiatry.net

Target Market(s)

Active working professionals.

Industry/Entity Type

Medical

Coding

Coded - Design and coding required

Number of Pages Required

4 page

Font styles to use
Sans Serif

Colors
6b449b

Requirements
Must have
• A modern look with logo and active images; clean and uncluttered. Visible phone number and address for call to action.
• 4 pages - Home, About Us, Services, Contact.
• Home page - update address & service logos.
• About Us - update of personal information.
• Services - Revamp of existing page.
• Contact page to include Google map, email & phone number.
Nice to have
• Ability to add content easily; eg. a blog or adding video onto Home page.
• Link to Facebook page.

```html
<!DOCTYPE html>
<html lang="en">
<head>
<meta charset="utf-8">
<title>Bramble Ridge Podiatry</title>
<link rel="stylesheet" href="https://fonts.googleapis.com/css2?family=Raleway:wght@400;500;600;700&family=Open+Sans:wght@400;600;700&display=swap">
<style>
:root{
  --purple:#4a2e94;
  --purple-dark:#3d2580;
  --purple-footer:#4d2f98;
  --purple-bar:#5a3ca8;
  --green:#7bc125;
  --orange:#f07d1c;
  --text:#444;
  --muted:#666;
  --light:#f0f0f0;
  --white:#fff;
}
*{margin:0;padding:0;box-sizing:border-box}
html,body{width:1200px;height:3035px;overflow:hidden}
body{font-family:"Open Sans",Arial,sans-serif;color:var(--text);background:var(--white);position:relative}
.abs{position:absolute}
.btn{position:absolute;display:flex;align-items:center;justify-content:center;background:var(--purple);color:var(--white);border-radius:30px;font-family:"Raleway",Arial,sans-serif;font-size:23px;font-weight:500;text-transform:uppercase}

/* hero */
.hero{position:absolute;left:0;top:0;width:1200px;height:800px}
.hero-photo{position:absolute;inset:0;background:linear-gradient(180deg,#5fb7ea 0%,#a8d8f2 30%,#7fa65a 55%,#3f6d2a 72%,#b7b0a1 82%,#8cb247 100%)}
.brand{position:absolute;left:430px;top:150px;width:440px;font-family:"Raleway",Arial,sans-serif;font-weight:700;font-size:56px;line-height:66px;color:var(--purple);display:flex;align-items:center;gap:22px}
.brand-dot{width:70px;height:70px;border-radius:50%;background:var(--purple);flex:none}
.hero-title{position:absolute;left:0;width:1200px;top:425px;text-align:center;color:var(--white);font-family:"Raleway",Arial,sans-serif;font-weight:700;font-size:50px;line-height:60px;text-transform:uppercase}
.hero .btn{left:486px;top:581px;width:228px;height:59px}

/* nav */
.nav-band{left:0;top:800px;width:1200px;height:62px;background:var(--purple)}
.nav{position:absolute;left:77px;top:800px;height:62px;display:flex}
.nav a{display:flex;align-items:center;height:62px;padding:0 35px;color:var(--white);font-family:"Raleway",Arial,sans-serif;font-size:18px;text-decoration:none;text-transform:uppercase}
.nav a.active{background:var(--green);width:123px;justify-content:center;padding:0}
.video-label{left:690px;top:800px;width:433px;height:62px;background:var(--green);color:var(--white);font-family:"Raleway",Arial,sans-serif;font-size:34px;display:flex;align-items:center;justify-content:center;text-transform:uppercase}
.video-frame{left:690px;top:864px;width:433px;height:312px;background:radial-gradient(ellipse at 45% 40%,#e8d8d8 0%,#b9a3a8 30%,#5b2848 70%,#3e1530 100%)}

/* welcome */
.welcome-kicker{left:77px;top:908px;font-family:"Raleway",Arial,sans-serif;font-size:31px;color:#555;text-transform:uppercase}
.welcome-title{left:77px;top:950px;font-family:"Raleway",Arial,sans-serif;font-size:41px;color:var(--purple);text-transform:uppercase;white-space:nowrap}
.welcome-text{left:77px;top:1020px;width:580px;font-size:15px;line-height:27px;color:var(--muted)}
.welcome .btn{left:77px;top:1125px;width:192px;height:49px}

/* appointment */
.appt{left:77px;top:1233px;width:1046px;height:255px;background:var(--light);border-bottom:5px solid var(--purple);box-shadow:0 28px 30px -20px rgba(0,0,0,.35)}
.appt-pointer{left:586px;top:1488px;width:0;height:0;border-left:14px solid transparent;border-right:14px solid transparent;border-top:14px solid var(--purple)}
.appt-photo{left:953px;top:1233px;width:170px;height:250px;background:linear-gradient(160deg,#f6dccb 0%,#e8b89c 55%,#f0f0f0 100%)}
.appt-title{left:77px;width:1046px;top:1258px;text-align:center;font-family:"Raleway",Arial,sans-serif;font-size:39px;color:var(--orange)}
.appt-call{left:77px;width:1046px;top:1325px;display:flex;justify-content:center;align-items:center;gap:12px;font-family:"Raleway",Arial,sans-serif;font-size:31px;color:var(--green)}
.appt-call strong{font-family:"Open Sans",Arial,sans-serif;font-weight:700;margin-left:12px}
.appt-or{left:77px;width:1046px;top:1392px;text-align:center;font-size:20px;color:#666}
.appt-email{left:77px;width:1046px;top:1428px;display:flex;justify-content:center;align-items:center;gap:8px;font-family:"Raleway",Arial,sans-serif;font-size:22px;color:var(--purple)}

/* services */
.section-title{left:0;width:1200px;text-align:center;font-family:"Raleway",Arial,sans-serif;font-size:44px;color:#555;text-transform:uppercase}
.section-title span{color:var(--purple)}
.services-title{top:1560px}
.service-divider{left:600px;top:1643px;width:2px;height:320px;background:#ddd}
.service{position:absolute;top:1643px;width:520px;text-align:center}
.service-photo{width:182px;height:182px;border-radius:50%;border:2px solid var(--purple);margin:0 auto;background:radial-gradient(circle at 50% 45%,#fbe9e0 0%,#e8c4b0 45%,#c9d6e2 100%)}
.service h3{margin-top:22px;font-family:"Raleway",Arial,sans-serif;font-weight:500;font-size:33px;color:var(--purple)}
.service p{margin-top:8px;font-size:15px;line-height:25px;color:var(--muted)}
.service .btn{position:relative;margin:14px auto 0;width:188px;height:51px}
.service-general{left:56px}
.service-special{left:600px}

/* news */
.news{left:0;top:2081px;width:1200px;height:502px;background:var(--light)}
.news-title{top:2138px}
.news-card{position:absolute;top:2204px;width:235px}
.news-photo{height:144px}
.news-card h4{margin-top:12px;font-weight:400;font-size:16px;line-height:26px;color:var(--purple)}
.news-date{display:flex;align-items:center;gap:6px;font-size:14px;color:#888;margin-top:2px}
.news-card p{margin-top:8px;font-size:15px;line-height:25px;color:var(--muted)}

/* partners */
.partner{position:absolute;top:2640px;height:80px;border-radius:8px}

/* footer */
.footer{left:0;top:2775px;width:1200px;height:208px;background:var(--purple-footer)}
.footer-item{position:absolute;top:2818px;width:400px;text-align:center;color:var(--white)}
.footer-icon{width:68px;height:68px;border-radius:50%;background:var(--purple-bar);margin:0 auto;display:flex;align-items:center;justify-content:center}
.footer-item p{margin-top:22px;font-size:15px;line-height:27px}
.footer-item p.phone{font-size:19px;font-weight:700}
.copyright-bar{left:0;top:2983px;width:1200px;height:52px;background:var(--purple-bar);color:var(--white);font-size:14px;display:flex;align-items:center;padding-left:80px}
.social{position:absolute;top:3002px;width:14px;height:14px;border-radius:50%;background:#b9aede}
</style>
</head>
<body>

<header class="hero">
  <div class="hero-photo" role="img" aria-label="Runner jogging along a sunny park path with trees and grass"></div>
  <div class="brand"><span class="brand-dot"></span><span>Bramble Ridge Podiatry</span></div>
  <h1 class="hero-title">Qualified Health<br>Professionals</h1>
  <a class="btn">Contact Us</a>
</header>

<div class="abs nav-band"></div>
<nav class="nav">
  <a class="active">Home</a><a>About</a><a>Services</a><a>Contact</a>
</nav>
<div class="abs video-label">Latest Video</div>
<div class="abs video-frame" role="img" aria-label="Video still of a podiatrist treating a foot with clinical instruments"></div>

<section class="welcome">
  <p class="abs welcome-kicker">Welcome to</p>
  <h2 class="abs welcome-title">Bramble Ridge Podiatry</h2>
  <p class="abs welcome-text">Bramble Ridge Podiatry is a Podiatry clinic in the heart of Melbourne CBD. We are located between Garnet &amp; Alder Streets in the Harlow Business Centre / Linden Court Complex.</p>
  <a class="btn">Read More</a>
</section>

<section>
  <div class="abs appt"></div>
  <div class="abs appt-pointer"></div>
  <div class="abs appt-photo" role="img" aria-label="Hands gently holding a bare foot"></div>
  <h2 class="abs appt-title">For Appointments or Enquiries</h2>
  <p class="abs appt-call">Please call us on
    <svg width="44" height="44" viewBox="0 0 44 44"><circle cx="22" cy="22" r="20" fill="none" stroke="#7bc125" stroke-width="2"/><path d="M15 13c2-1 3 0 4 3l1 3c0 1-1 2-2 2 1 3 3 5 6 6 0-1 1-2 2-2l3 1c3 1 4 2 3 4-1 2-3 3-5 2-6-2-11-7-13-13-1-2 0-5 1-6z" fill="#7bc125"/></svg>
    <strong>1300 482 907</strong></p>
  <p class="abs appt-or">OR</p>
  <p class="abs appt-email">Email:
    <svg width="24" height="18" viewBox="0 0 24 18"><rect x="1" y="1" width="22" height="16" rx="1" fill="none" stroke="#4a2e94" stroke-width="2"/><path d="M1 2l11 9 11-9" fill="none" stroke="#4a2e94" stroke-width="2"/></svg>
    info@brambleridgepodiatry.net</p>
</section>

<section>
  <h2 class="abs section-title services-title">Services <span>We Provide</span></h2>
  <div class="abs service-divider"></div>
  <div class="service service-general">
    <div class="service-photo" role="img" aria-label="Podiatrist examining the sole of a foot"></div>
    <h3>General Treatment</h3>
    <p>Nails, Corns, Callus, Warts, Skin Disorders, Heel pain /<br>Heel Spurs / Arch pain - plantar Fasciitis</p>
    <a class="btn">Read More</a>
  </div>
  <div class="service service-special">
    <div class="service-photo" role="img" aria-label="Nail treatment on a toe with a clinical tool"></div>
    <h3>Specialised Treatments</h3>
    <p>Diabetic Management, Nail Surgery, Biomechanical<br>Assessment, Gait Analysis, Orthotic Therapy</p>
    <a class="btn">Read More</a>
  </div>
</section>

<section>
  <div class="abs news"></div>
  <h2 class="abs section-title news-title">Latest <span>News</span></h2>
  <article class="news-card" style="left:77px">
    <div class="news-photo" role="img" aria-label="Practitioner assessing a patient's leg in a clinic" style="background:linear-gradient(135deg,#d9d4cc,#8a8278 60%,#eeeeee)"></div>
    <h4>Lorem Ipsum is dummy text and simply printing.</h4>
    <div class="news-date"><svg width="12" height="12" viewBox="0 0 12 12"><rect x="1" y="2" width="10" height="9" fill="none" stroke="#999" stroke-width="1.4"/><path d="M1 5h10" stroke="#999" stroke-width="1.4"/></svg>01 August 2016</div>
    <p>Lorem Ipsum is simply dummy text of the printing and type setting industry.</p>
  </article>
  <article class="news-card" style="left:348px">
    <div class="news-photo" role="img" aria-label="Bare feet walking along a wet beach shoreline" style="background:linear-gradient(180deg,#5b4a3e,#9d8a78 50%,#c9b9a6)"></div>
    <h4>Lorem Ipsum is dummy text and simply printing.</h4>
    <div class="news-date"><svg width="12" height="12" viewBox="0 0 12 12"><rect x="1" y="2" width="10" height="9" fill="none" stroke="#999" stroke-width="1.4"/><path d="M1 5h10" stroke="#999" stroke-width="1.4"/></svg>01 August 2016</div>
    <p>Lorem Ipsum is simply dummy text of the printing and type setting industry.</p>
  </article>
  <article class="news-card" style="left:619px">
    <div class="news-photo" role="img" aria-label="Foot anatomy view highlighting heel pain" style="background:radial-gradient(circle at 55% 65%,#e86a5a 0%,#b8c3d6 35%,#f2f2f2 80%)"></div>
    <h4>Lorem Ipsum is dummy text and simply printing.</h4>
    <div class="news-date"><svg width="12" height="12" viewBox="0 0 12 12"><rect x="1" y="2" width="10" height="9" fill="none" stroke="#999" stroke-width="1.4"/><path d="M1 5h10" stroke="#999" stroke-width="1.4"/></svg>01 August 2016</div>
    <p>Lorem Ipsum is simply dummy text of the printing and type setting industry.</p>
  </article>
  <article class="news-card" style="left:890px">
    <div class="news-photo" role="img" aria-label="Consultation between a practitioner and a patient" style="background:linear-gradient(135deg,#f4efe9,#d9b9a3 55%,#e9e2dc)"></div>
    <h4>Lorem Ipsum is dummy text and simply printing.</h4>
    <div class="news-date"><svg width="12" height="12" viewBox="0 0 12 12"><rect x="1" y="2" width="10" height="9" fill="none" stroke="#999" stroke-width="1.4"/><path d="M1 5h10" stroke="#999" stroke-width="1.4"/></svg>01 August 2016</div>
    <p>Lorem Ipsum is simply dummy text of the printing and type setting industry.</p>
  </article>
</section>

<section aria-label="Affiliations">
  <div class="partner" style="left:80px;width:225px;background:#d6deef"></div>
  <div class="partner" style="left:345px;width:240px;background:#e3e3e3"></div>
  <div class="partner" style="left:625px;width:220px;background:#cfe8d6"></div>
  <div class="partner" style="left:900px;width:215px;background:#d4e2f2"></div>
</section>

<footer>
  <div class="abs footer"></div>
  <div class="footer-item" style="left:29px">
    <div class="footer-icon"><svg width="22" height="28" viewBox="0 0 22 28"><path d="M11 1C5 1 1 5 1 11c0 7 10 16 10 16s10-9 10-16C21 5 17 1 11 1z" fill="#fff"/><circle cx="11" cy="11" r="3.5" fill="#5a3ca8"/></svg></div>
    <p>Suite 214 / 76 Harlow Street<br>Melbourne 3000</p>
  </div>
  <div class="footer-item" style="left:399px">
    <div class="footer-icon"><svg width="26" height="26" viewBox="0 0 26 26"><path d="M5 2c2-1 3 0 4 3l1 3c0 1-1 2-2 3 1 3 4 6 7 7 1-1 2-2 3-2l3 1c3 1 4 2 3 4-1 2-3 4-6 3C11 22 4 15 2 8 1 5 3 3 5 2z" fill="#fff"/></svg></div>
    <p class="phone">1300 482 907</p>
  </div>
  <div class="footer-item" style="left:755px">
    <div class="footer-icon"><svg width="26" height="20" viewBox="0 0 26 20"><rect x="1" y="1" width="24" height="18" rx="2" fill="none" stroke="#fff" stroke-width="2"/><path d="M1 3l12 9 12-9" fill="none" stroke="#fff" stroke-width="2"/></svg></div>
    <p>info@brambleridgepodiatry.net</p>
  </div>
  <div class="abs copyright-bar">© Bramble Ridge Podiatry- 2016. All Rights Reserved.</div>
  <span class="social" style="left:1022px"></span>
  <span class="social" style="left:1062px"></span>
  <span class="social" style="left:1103px"></span>
</footer>

</body>
</html>
```